Web design for financial services

A modern web design of financial services (brokerage firm)
Req.s and technology tags :
- Very mobile friendly.
- One paged with some inner pages.
- Animated sticky header .
- Member login area for e-trade.
- Support RTL language.
- HTML & CSS.

The logo will be Home link
• MPTR :
WHO WE ARE
Content :
i) Board of Directors
ii) Mission Statement
iii) Corporate Values
iv) Regulations
• Financial Services :
WHAT WE DO
Content:
i) Electronic trading
ii) Trading desk
iii) Institutional
iv) Investors Education
• News
• Market Tools
• Forms---- opens new page
• Careers---- opens new page
• Contact Us----opens new page

The website is :
http://www.mptr-doha-example.com/

The logo need some changes to be more modern and impressively , but with keeping same structure .

Some related websites :
https://www.lv-bourse.example/

financial market

Financial Service

Coded - Design and coding required

2 page

• same fonts of http://www.kwdholdings.example/

• - Very mobile friendly.
• - One paged with some inner pages.
• - Animated sticky header .
• - Member login area for e-trade.
• - Support RTL language.
• - HTML & CSS.
• Slider , some Qatari theme,
• i like the video inside the home page
• ex :http://www.kwdholdings.example/

```html
<!DOCTYPE html>
<html lang="en">
<head>
<meta charset="utf-8">
<title>MPTR — Meridian Pearl Trade Securities Company</title>
<link rel="stylesheet" href="https://fonts.googleapis.com/css2?family=Open+Sans:wght@400;600;700&display=swap">
<style>
:root{
  --red:#9c2b2c;
  --red-dark:#8a2425;
  --ink:#2b2b2b;
  --text:#555;
  --muted:#8a8a8a;
  --line:#dcdcdc;
  --grey-band:#8e8e8e;
  --white:#fff;
}
*{box-sizing:border-box;margin:0;padding:0}
html,body{width:1200px;height:2965px;overflow:hidden}
body{font-family:"Open Sans",Arial,sans-serif;color:var(--text);background:var(--white);position:relative}
a{color:inherit;text-decoration:none}

/* header */
.site-header{position:absolute;top:0;left:0;width:1200px;height:92px;background:var(--white);z-index:5}
.brand{position:absolute;left:86px;top:4px;width:150px;height:150px;border-radius:50%;background:var(--white);display:flex;align-items:center;justify-content:center;font-weight:700;font-size:34px;color:var(--red);letter-spacing:1px;z-index:6}
.top-bar{position:absolute;right:50px;top:12px;display:flex;align-items:center;gap:22px}
.login-btn{border:1.5px solid var(--red);color:var(--red);border-radius:20px;padding:5px 18px;font-size:14px;font-weight:600;display:flex;align-items:center;gap:6px}
.lang{display:flex;align-items:center;gap:8px;font-size:14px;font-weight:600;color:var(--ink)}
.main-nav{position:absolute;right:50px;top:60px;display:flex;gap:34px;font-size:15px;font-weight:700;color:var(--ink)}
.main-nav .active{color:var(--red)}

/* hero */
.hero{position:absolute;top:92px;left:0;width:1200px;height:448px;background:linear-gradient(180deg,#2b3350 0%,#3b3e56 45%,#5b4a3a 80%,#3a2e24 100%);text-align:center;color:var(--white)}
.hero-title{position:absolute;top:150px;width:100%}
.hero-title .line-1{display:block;font-size:50px;font-weight:400;line-height:60px}
.hero-title .line-2{display:block;font-size:64px;font-weight:600;line-height:76px}
.play-btn{position:absolute;left:572px;top:344px;width:56px;height:56px}

/* who we are */
.who{position:absolute;top:540px;left:0;width:1200px;height:418px}
.section-title{font-size:30px;font-weight:700;color:var(--ink)}
.who .section-title{position:absolute;left:99px;top:58px}
.who-body{position:absolute;left:99px;top:118px;width:540px}
.who-text{font-size:12px;line-height:26px}
.who-text p+p{margin-top:22px}
.outline-btn{display:inline-block;border:1.5px solid var(--line);border-radius:24px;padding:9px 26px;font-size:14px;font-weight:700;color:var(--ink)}
.who .outline-btn{margin-top:28px}
.who-photo{position:absolute;left:650px;top:68px;width:452px;height:290px;border:6px solid #f1f1f1;box-shadow:0 0 0 1px var(--line);background:linear-gradient(135deg,#e9ecef 0%,#d3d8dc 55%,#a7aeb4 100%)}

/* what we do */
.services{position:absolute;top:958px;left:0;width:1200px;height:506px;background:linear-gradient(135deg,var(--red) 0%,var(--red-dark) 100%);color:var(--white);text-align:center}
.services .section-title{color:var(--white);position:absolute;top:52px;width:100%}
.services .lead{position:absolute;top:104px;width:100%;font-size:15px;font-weight:600}
.service{position:absolute;top:164px;width:240px}
.service .icon{width:168px;height:168px;margin:0 auto}
.service h3{margin-top:28px;font-size:16px;font-weight:700}
.service p{margin-top:8px;font-size:12.5px;line-height:21px}
.read-more{display:block;margin-top:12px;font-size:12.5px;font-weight:700}
.slider-arrow{position:absolute;width:38px;height:38px;border-radius:50%;display:flex;align-items:center;justify-content:center}
.services .slider-arrow{background:rgba(0,0,0,.18);top:292px}

/* news */
.news{position:absolute;top:1464px;left:0;width:1200px;height:534px}
.news .section-title{position:absolute;top:52px;width:100%;text-align:center}
.news-card{position:absolute;top:126px;width:322px}
.news-photo{position:relative;height:210px;border:5px solid #f1f1f1;box-shadow:0 0 0 1px var(--line)}
.date-tag{position:absolute;left:-5px;bottom:0;width:54px;height:62px;background:var(--red);color:var(--white);text-align:center;font-weight:700;font-size:22px;line-height:30px;padding-top:4px}
.date-tag small{display:block;font-size:12px;font-weight:600;line-height:16px}
.news-card h3{margin-top:20px;font-size:18px;font-weight:600;color:var(--ink)}
.news-card p{margin-top:8px;font-size:12.5px;line-height:21px}
.news-meta{margin-top:16px;border-top:1px solid var(--line);padding-top:14px;font-size:12px;display:flex;gap:22px}
.news-meta span{display:flex;align-items:center;gap:6px}

/* partners */
.partners{position:absolute;top:1998px;left:99px;width:1002px;height:218px;border-top:1px solid var(--line)}
.partner{position:absolute;top:50px;width:217px;height:104px;border:1px solid var(--line);box-shadow:0 1px 3px rgba(0,0,0,.08);display:flex;align-items:center;justify-content:center}
.partner span{width:130px;height:34px;background:#c9c9c9;border-radius:4px}
.partners .slider-arrow{border:1.5px solid var(--line);top:82px;background:var(--white)}

/* market tools */
.tools{position:absolute;top:2216px;left:0;width:1200px;height:412px;background:var(--grey-band);color:var(--white);text-align:center}
.tools .section-title{color:var(--white);position:absolute;top:44px;width:100%}
.tool{position:absolute;top:112px;width:300px}
.tool .icon{width:100px;height:100px;margin:0 auto}
.tool h3{margin-top:20px;font-size:18px;font-weight:700}
.tool p{margin-top:6px;font-size:12.5px;line-height:20.5px}

/* footer */
.site-footer{position:absolute;top:2628px;left:0;width:1200px;height:337px}
.footer-brand{position:absolute;left:140px;top:40px;width:170px;height:170px;border-radius:50%;border:2px solid var(--line);display:flex;align-items:center;justify-content:center;font-weight:700;font-size:40px;color:var(--red)}
.footer-col{position:absolute;top:62px}
.footer-col h4{font-size:16px;font-weight:600;color:var(--ink);margin-bottom:16px}
.footer-links li{list-style:none;font-size:12.5px;line-height:23px}
.footer-col p{font-size:12.5px;line-height:21px}
.email-field{margin-top:16px;width:250px;border-bottom:1px solid var(--line);padding:8px 0;font-size:12px;color:#aaa}
.subscribe-btn{margin-top:18px;display:inline-block;border:1.5px solid var(--line);border-radius:16px;padding:4px 14px;font-size:11px;font-weight:700;color:var(--red)}
.contact-list li{list-style:none;display:flex;gap:16px;font-size:12px;line-height:20px;margin-bottom:13px;white-space:nowrap}
.contact-list svg{flex:none;margin-top:2px}
.footer-bottom{position:absolute;left:99px;top:264px;width:1002px;border-top:1px solid var(--line);padding-top:26px;display:flex;justify-content:space-between;align-items:center;font-size:12.5px}
.social{display:flex;gap:8px}
.social span{width:26px;height:26px;border:1.5px solid var(--line);border-radius:50%;display:block;position:relative}
.social span::after{content:"";position:absolute;left:8px;top:8px;width:7px;height:7px;border-radius:50%;background:var(--red)}
</style>
</head>
<body>

<header class="site-header">
  <a class="brand" href="#">MPTR</a>
  <div class="top-bar">
    <a class="login-btn" href="#">
      <svg width="10" height="12" viewBox="0 0 10 12"><rect x="0" y="5" width="10" height="7" rx="1" fill="#9c2b2c"/><path d="M2.5 5V3.5a2.5 2.5 0 0 1 5 0V5" fill="none" stroke="#9c2b2c" stroke-width="1.5"/></svg>
      LOGIN
    </a>
    <div class="lang">
      <svg width="26" height="26" viewBox="0 0 26 26"><circle cx="13" cy="13" r="13" fill="#2b3d7a"/><rect x="10" y="0" width="6" height="26" fill="#fff"/><rect x="0" y="10" width="26" height="6" fill="#fff"/><rect x="11.5" y="0" width="3" height="26" fill="#c8202f"/><rect x="0" y="11.5" width="26" height="3" fill="#c8202f"/></svg>
      ENGLISH
      <svg width="8" height="5" viewBox="0 0 8 5"><path d="M0 0h8L4 5z" fill="#2b2b2b"/></svg>
    </div>
  </div>
  <nav class="main-nav">
    <a class="active" href="#">MPTR</a>
    <a href="#">FINANCIAL SERVICE</a>
    <a href="#">NEWS</a>
    <a href="#">MARKET TOOL</a>
    <a href="#">FORMS</a>
    <a href="#">CAREERS</a>
  </nav>
</header>

<section class="hero" role="img" aria-label="Night skyline of Doha towers over the bay">
  <h1 class="hero-title">
    <span class="line-1">Meridian Pearl</span>
    <span class="line-2">Trade Securities Company</span>
  </h1>
  <svg class="play-btn" viewBox="0 0 56 56"><circle cx="28" cy="28" r="26" fill="rgba(0,0,0,.55)" stroke="#fff" stroke-width="2.5"/><path d="M22 17l17 11-17 11z" fill="#fff"/></svg>
</section>

<section class="who">
  <h2 class="section-title">WHO WE ARE</h2>
  <div class="who-body">
    <div class="who-text">
      <p>Meridian Pearl Trade Securities is a private Qatari company that aims to provide secure and technologically advanced methods of trading to its clients.</p>
      <p>Those facilities enables clients to trade faster, more secure &amp; private. Having this strategy in our in minds, with this online portal we begin. We intent to optimize all company resources to position ourselves as an unique competitive business model with the goal of generating highly competitive returns for our clients and shareholders.</p>
    </div>
    <a class="outline-btn" href="#">ABOUT MPTR</a>
  </div>
  <div class="who-photo" role="img" aria-label="Business meeting in a bright modern office"></div>
</section>

<section class="services">
  <h2 class="section-title">WHAT WE DO</h2>
  <p class="lead">Meridian Pearl Trade Securities offers various trading &amp; investment services:</p>

  <span class="slider-arrow" style="left:33px"><svg width="10" height="14" viewBox="0 0 10 14"><path d="M8 1L2 7l6 6" fill="none" stroke="#fff" stroke-width="2"/></svg></span>
  <span class="slider-arrow" style="right:33px"><svg width="10" height="14" viewBox="0 0 10 14"><path d="M2 1l6 6-6 6" fill="none" stroke="#fff" stroke-width="2"/></svg></span>

  <div class="service" style="left:85px">
    <svg class="icon" viewBox="0 0 168 168"><circle cx="84" cy="84" r="82" fill="#fff"/><rect x="58" y="64" width="52" height="34" rx="3" fill="none" stroke="#9c2b2c" stroke-width="4"/><rect x="64" y="71" width="14" height="14" fill="#9c2b2c"/><rect x="82" y="72" width="22" height="3" fill="#9c2b2c"/><rect x="82" y="80" width="22" height="3" fill="#9c2b2c"/><path d="M76 98v8h16v-8M68 108h32" fill="none" stroke="#9c2b2c" stroke-width="4"/></svg>
    <h3>Trading Account registration</h3>
    <p>Those facilities enables clients to trade faster, more secure &amp; private.</p>
    <a class="read-more" href="#">READ MORE &gt;&gt;</a>
  </div>
  <div class="service" style="left:347px">
    <svg class="icon" viewBox="0 0 168 168"><circle cx="84" cy="84" r="82" fill="#fff"/><rect x="58" y="62" width="52" height="36" rx="3" fill="none" stroke="#9c2b2c" stroke-width="4"/><path d="M68 72l10 8-4 1 4 7-3 1-4-7-3 3z" fill="#9c2b2c"/><path d="M76 98v8h16v-8M68 108h32" fill="none" stroke="#9c2b2c" stroke-width="4"/></svg>
    <h3>Electronic Registration</h3>
    <p>Those facilities enables clients to trade faster, more secure &amp; private.</p>
    <a class="read-more" href="#">READ MORE &gt;&gt;</a>
  </div>
  <div class="service" style="left:611px">
    <svg class="icon" viewBox="0 0 168 168"><circle cx="84" cy="84" r="82" fill="#fff"/><text x="84" y="74" text-anchor="middle" font-family="Open Sans,sans-serif" font-weight="700" font-size="22" fill="#9c2b2c">$</text><path d="M56 80h8l8 24h30l6-18H68" fill="none" stroke="#9c2b2c" stroke-width="4" stroke-linejoin="round"/><circle cx="76" cy="112" r="4" fill="#9c2b2c"/><circle cx="98" cy="112" r="4" fill="#9c2b2c"/></svg>
    <h3>Buy &amp; Sell Order Execution</h3>
    <p>Those facilities enables clients to trade faster, more secure &amp; private.</p>
    <a class="read-more" href="#">READ MORE &gt;&gt;</a>
  </div>
  <div class="service" style="left:875px">
    <svg class="icon" viewBox="0 0 168 168"><circle cx="84" cy="84" r="82" fill="#fff"/><circle cx="72" cy="74" r="14" fill="#9c2b2c"/><text x="72" y="80" text-anchor="middle" font-family="Open Sans,sans-serif" font-weight="700" font-size="16" fill="#fff">$</text><circle cx="98" cy="98" r="14" fill="#9c2b2c"/><text x="98" y="104" text-anchor="middle" font-family="Open Sans,sans-serif" font-weight="700" font-size="16" fill="#fff">€</text><path d="M92 64a18 18 0 0 1 16 16M76 108a18 18 0 0 1-16-16" fill="none" stroke="#9c2b2c" stroke-width="3"/></svg>
    <h3>Electronic Trade</h3>
    <p>Those facilities enables clients to trade faster, more secure &amp; private.</p>
    <a class="read-more" href="#">READ MORE &gt;&gt;</a>
  </div>
</section>

<section class="news">
  <h2 class="section-title">LATEST NEWS</h2>

  <article class="news-card" style="left:99px">
    <div class="news-photo" role="img" aria-label="Two colleagues reviewing a tablet at a café table" style="background:linear-gradient(135deg,#d9d6d2,#b9b2ab 60%,#8d8378)"><div class="date-tag">01<small>NOV</small></div></div>
    <h3>Finibus Bonorum et Malorum</h3>
    <p>Nam libero tempore, cum soluta nobis est eligendi optio cumque nihil impedit quo minus id quod maxim.</p>
    <div class="news-meta"><span><svg width="10" height="11" viewBox="0 0 10 11"><circle cx="5" cy="3" r="3" fill="#9c2b2c"/><path d="M0 11a5 5 0 0 1 10 0z" fill="#9c2b2c"/></svg>John Doe</span><span><svg width="13" height="11" viewBox="0 0 13 11"><path d="M1 1h9v6H5l-3 3V7H1z" fill="none" stroke="#9c2b2c" stroke-width="1.4"/></svg>3 Comments</span></div>
  </article>

  <article class="news-card" style="left:442px">
    <div class="news-photo" role="img" aria-label="Hands over charts and a laptop on a wooden desk" style="background:linear-gradient(135deg,#5a5148,#a08b72 55%,#d8d2c8)"><div class="date-tag">01<small>NOV</small></div></div>
    <h3>Finibus Bonorum et Malorum</h3>
    <p>Nam libero tempore, cum soluta nobis est eligendi optio cumque nihil impedit quo minus id quod maxim.</p>
    <div class="news-meta"><span><svg width="10" height="11" viewBox="0 0 10 11"><circle cx="5" cy="3" r="3" fill="#9c2b2c"/><path d="M0 11a5 5 0 0 1 10 0z" fill="#9c2b2c"/></svg>John Doe</span><span><svg width="13" height="11" viewBox="0 0 13 11"><path d="M1 1h9v6H5l-3 3V7H1z" fill="none" stroke="#9c2b2c" stroke-width="1.4"/></svg>3 Comments</span></div>
  </article>

  <article class="news-card" style="left:784px">
    <div class="news-photo" role="img" aria-label="Presenter at a whiteboard in a training room" style="background:linear-gradient(135deg,#eceeef,#cfd3d6 60%,#9ea5aa)"><div class="date-tag">01<small>NOV</small></div></div>
    <h3>Finibus Bonorum et Malorum</h3>
    <p>Nam libero tempore, cum soluta nobis est eligendi optio cumque nihil impedit quo minus id quod maxim.</p>
    <div class="news-meta"><span><svg width="10" height="11" viewBox="0 0 10 11"><circle cx="5" cy="3" r="3" fill="#9c2b2c"/><path d="M0 11a5 5 0 0 1 10 0z" fill="#9c2b2c"/></svg>John Doe</span><span><svg width="13" height="11" viewBox="0 0 13 11"><path d="M1 1h9v6H5l-3 3V7H1z" fill="none" stroke="#9c2b2c" stroke-width="1.4"/></svg>3 Comments</span></div>
  </article>
</section>

<section class="partners" aria-label="Partners">
  <span class="slider-arrow" style="left:-68px"><svg width="10" height="14" viewBox="0 0 10 14"><path d="M8 1L2 7l6 6" fill="none" stroke="#999" stroke-width="2"/></svg></span>
  <div class="partner" style="left:0"><span></span></div>
  <div class="partner" style="left:262px"><span></span></div>
  <div class="partner" style="left:524px"><span></span></div>
  <div class="partner" style="left:785px"><span></span></div>
  <span class="slider-arrow" style="right:-68px"><svg width="10" height="14" viewBox="0 0 10 14"><path d="M2 1l6 6-6 6" fill="none" stroke="#999" stroke-width="2"/></svg></span>
</section>

<section class="tools">
  <h2 class="section-title">MARKET TOOLS</h2>

  <div class="tool" style="left:98px">
    <svg class="icon" viewBox="0 0 100 100"><path d="M22 90V52h20v38M42 90V40h36v50M10 90h80" fill="none" stroke="#fff" stroke-width="4"/><path d="M32 34a10 10 0 1 1 20 0c0 9-10 18-10 18S32 43 32 34z" fill="none" stroke="#fff" stroke-width="4"/><circle cx="42" cy="34" r="3.5" fill="#fff"/><g fill="#fff"><rect x="50" y="50" width="8" height="8"/><rect x="64" y="50" width="8" height="8"/><rect x="50" y="64" width="8" height="8"/><rect x="64" y="64" width="8" height="8"/><rect x="28" y="62" width="8" height="8"/></g></svg>
    <h3>Most Active Company</h3>
    <p>Those facilities enables clients to trade faster, more secure &amp; private. Having this strategy in our in minds, with this online portal we begin.</p>
    <a class="read-more" href="#">READ MORE &gt;&gt;</a>
  </div>
  <div class="tool" style="left:450px">
    <svg class="icon" viewBox="0 0 100 100"><g fill="#fff"><rect x="8" y="70" width="14" height="22"/><rect x="28" y="58" width="14" height="34"/><rect x="48" y="64" width="14" height="28"/><rect x="68" y="44" width="14" height="48"/></g><path d="M8 56l22-20 16 12 34-32" fill="none" stroke="#fff" stroke-width="5"/><path d="M70 10h18v18z" fill="#fff"/></svg>
    <h3>Top Gainer</h3>
    <p>Those facilities enables clients to trade faster, more secure &amp; private. Having this strategy in our in minds, with this online portal we begin.</p>
    <a class="read-more" href="#">READ MORE &gt;&gt;</a>
  </div>
  <div class="tool" style="left:800px">
    <svg class="icon" viewBox="0 0 100 100"><g fill="#fff"><rect x="16" y="50" width="12" height="42"/><rect x="34" y="60" width="12" height="32"/><rect x="52" y="66" width="12" height="26"/><rect x="70" y="72" width="12" height="20"/></g><path d="M14 14c20 4 40 14 58 34" fill="none" stroke="#fff" stroke-width="4"/><path d="M78 56l-2-16-12 8z" fill="#fff"/></svg>
    <h3>Top Loser</h3>
    <p>Those facilities enables clients to trade faster, more secure &amp; private. Having this strategy in our in minds, with this online portal we begin.</p>
    <a class="read-more" href="#">READ MORE &gt;&gt;</a>
  </div>
</section>

<footer class="site-footer">
  <a class="footer-brand" href="#">MPTR</a>

  <div class="footer-col" style="left:398px">
    <h4>Information</h4>
    <ul class="footer-links">
      <li>MPTR</li><li>Financial Service</li><li>News</li><li>Market Tool</li><li>Forms</li><li>Careers</li>
    </ul>
  </div>

  <div class="footer-col" style="left:586px;width:260px">
    <h4>Newsletter Subscription</h4>
    <p>Register your Email Address to get information about us</p>
    <div class="email-field">Email Address</div>
    <span class="subscribe-btn">SUBSCRIBE</span>
  </div>

  <div class="footer-col" style="left:898px;width:270px">
    <h4>Contact Us</h4>
    <ul class="contact-list">
      <li><svg width="10" height="14" viewBox="0 0 10 14"><path d="M5 0a5 5 0 0 1 5 5c0 4-5 9-5 9S0 9 0 5a5 5 0 0 1 5-5z" fill="#9c2b2c"/><circle cx="5" cy="5" r="2" fill="#fff"/></svg><span>Second Floor, Nakheel Plaza,<br>Corniche Road-opposite Harbour Mall</span></li>
      <li><svg width="12" height="12" viewBox="0 0 12 12"><path d="M2 0l3 3-1.5 2a7 7 0 0 0 3.5 3.5L9 7l3 3-2 2C5 12 0 7 0 2z" fill="#9c2b2c"/></svg><span>+974 40001234</span></li>
      <li><svg width="12" height="12" viewBox="0 0 12 12"><rect x="0" y="4" width="12" height="8" rx="1" fill="#9c2b2c"/><rect x="3" y="0" width="6" height="5" fill="none" stroke="#9c2b2c" stroke-width="1.4"/></svg><span>+974 40005678</span></li>
      <li><svg width="12" height="10" viewBox="0 0 12 10"><rect width="12" height="10" rx="1" fill="#9c2b2c"/><path d="M0 1l6 4 6-4" fill="none" stroke="#fff" stroke-width="1.2"/></svg><span>info@mptr-doha-example.com</span></li>
    </ul>
  </div>

  <div class="footer-bottom">
    <span>Copyrights © 2017, MPTR. All rights reserved.</span>
    <div class="social"><span></span><span></span><span></span><span></span></div>
  </div>
</footer>

</body>
</html>
```